Website for a company offering full serivce charging solutions for electric cars

The company "tanu-werk" (english: "tanu-works") offering all-in-one-solutions for charging infrastructure for electric mobility.

There are four products:
1- Wallboxes for single-family homes
2- Solutions for property devloper/-management for property parking space
3- All-in-one-charging solution for municipalities/communities
4- Solutions for tourism/hotels/holiday appartments

The Website structure:
1. Main Page
2.1. Product Page Single Homes
2.2. Product Page Property Management / Parking
2.3. Product Page Municipality
2.4. Product Page Tourism
3. Contact Form / Request for information
4. Imprint / Legal

The Website should be built on Wordpress with a powerful possibility to simply add/modify specific landing pages.

We would like you to implement the website later and also maintain it if possible, but we would be able to do minor modifications by ourselfs (for A/B-Testing)

The website should be clear and simple, easy to understand.
Target group is mainly B2C without deeper knowledge of that topic.

It should suggest, that we will provide a very simple way to get the charging infrastructure done.

We need a contact form, maybe we will use Hubspot later.

Attached you will find a draft of the main page and a landing page (for 2.2) - it is just the content, please ignore the design. We would love to let you create a suitable design.
Also you will find some drafts a bit different for the same story.

I added also a few stock photos, but they don't need to be used! If you have better ideas, you are welcome!

Industry/Entity Type

Charging/Electric mobility

Number of Pages Required

2 page

Font styles to use
Sans Serif

Requirements
Must have
• Based on Wordpress, and the designer should be able to implement it on Wordpress on a later step

```html
<!DOCTYPE html>
<html lang="de">
<head>
<meta charset="utf-8">
<title>tanu-werk – Lösungen</title>
<link rel="stylesheet" href="https://fonts.googleapis.com/css2?family=Ubuntu:wght@500;700&family=Encode+Sans:wght@400;500&display=swap">
<style>
:root{
  --bg:#0f1626;
  --bg-footer:#181e29;
  --pink:#ec1aa0;
  --purple:#7a5cc8;
  --white:#ffffff;
  --muted:#e6e6ee;
}
*{margin:0;padding:0;box-sizing:border-box}
html,body{width:701px;height:1200px;overflow:hidden}
body{background:var(--bg);color:var(--white);font-family:"Encode Sans",sans-serif;position:relative}

.site-header{position:absolute;top:0;left:0;width:701px;height:60px;background:var(--bg);z-index:2}
.brand{position:absolute;left:65px;top:20px;font-family:"Ubuntu",sans-serif;font-weight:500;font-size:15px;color:var(--white);display:flex;align-items:center;gap:6px}
.brand-dot{width:10px;height:10px;border-radius:50%;background:var(--pink)}
.main-nav{position:absolute;top:25px;left:321px;display:flex;gap:0;font-size:9px;font-weight:500}
.main-nav a{color:var(--white);text-decoration:none;margin-right:29px}
.main-nav a.is-active{color:var(--pink)}

.hero{position:absolute;top:60px;left:0;width:701px;height:325px}
.hero-photo{position:absolute;inset:0;background:
  radial-gradient(ellipse at 72% 55%,rgba(60,90,170,.55),transparent 55%),
  linear-gradient(90deg,#2a2540 0%,#3b3560 45%,#4a4866 62%,#243564 85%,#1b2a66 100%)}
.hero-content{position:absolute;left:65px;top:51px;width:340px}
.hero-eyebrow{font-family:"Ubuntu",sans-serif;font-weight:500;font-size:12px;color:var(--pink);margin-bottom:7px}
.hero-title{font-family:"Ubuntu",sans-serif;font-weight:500;font-size:19.5px;line-height:25px;margin-bottom:9px}
.hero-text{font-size:8.6px;line-height:15px;width:310px;margin-bottom:14px}
.btn-primary{display:inline-block;width:91px;height:30px;line-height:30px;text-align:center;border-radius:15px;font-family:"Ubuntu",sans-serif;font-weight:500;font-size:8.5px;color:var(--white);background:linear-gradient(90deg,var(--purple),var(--pink))}

.solutions{position:absolute;top:385px;left:0;width:701px;height:608px}
.solution{position:absolute;top:50px;width:198px}
.solution h2{font-family:"Ubuntu",sans-serif;font-weight:500;font-size:15px;color:var(--pink);text-align:center;height:31px}
.solution-box{border:3px solid;border-image:linear-gradient(180deg,var(--pink),var(--purple)) 1;padding:19px 8px 0 11px}
.solution-box.is-featured{border:none;padding:21px 11px 0 13px;background:linear-gradient(160deg,#8a55c2 0%,#c43cc0 55%,#e02fb0 100%)}
.solution ul{list-style:none}
.solution li{position:relative;padding-left:16px;font-size:8.6px;line-height:15px;hyphens:auto}
.solution li::before{content:"";position:absolute;left:0;top:4px;width:5px;height:5px;border:1.6px solid var(--pink);border-radius:50%;box-shadow:inset 0 0 0 1.2px transparent;background:radial-gradient(circle,var(--pink) 40%,transparent 45%)}
.is-featured li::before{border-color:var(--white);background:radial-gradient(circle,var(--white) 40%,transparent 45%)}
.col-private{left:38px}.col-private .solution-box{height:323px}
.col-business{left:251px}.col-business .solution-box{height:489px}
.col-community{left:464px}.col-community .solution-box{height:262px}

.site-footer{position:absolute;top:993px;left:0;width:701px;height:207px;background:var(--bg-footer);text-align:center}
.footer-brand{position:absolute;top:38px;left:0;width:701px;display:flex;justify-content:center;align-items:center;gap:7px;font-family:"Ubuntu",sans-serif;font-weight:500;font-size:17px}
.footer-nav{position:absolute;top:82px;left:197px;display:flex;font-size:9px}
.footer-nav a{color:var(--white);text-decoration:none;margin-right:28px}
.social{position:absolute;top:1114px;top:121px;left:297px;display:flex;gap:6px}
.social span{width:22px;height:22px;border-radius:50%;border:1px solid var(--white)}
.social span.is-active{border:none;background:linear-gradient(90deg,var(--purple),var(--pink))}
.copyright{position:absolute;top:164px;left:0;width:701px;font-size:8.6px}
</style>
</head>
<body>
<header class="site-header">
  <div class="brand"><span class="brand-dot"></span>tanu-werk.de</div>
  <nav class="main-nav">
    <a class="is-active" href="#">Lösungen</a><a href="#">Unternehmen</a><a href="#">Services</a><a href="#">Karriere</a><a href="#">Kontakt</a>
  </nav>
</header>

<section class="hero">
  <div class="hero-photo" role="img" aria-label="Foto: Ladestecker steckt in einer Ladesäule für E-Autos, violett-blau getönt"></div>
  <div class="hero-content">
    <p class="hero-eyebrow">Tanu-werk ist Ihr Partner</p>
    <h1 class="hero-title">Wenn das Laden nicht nur einfach, sondern die Umsetzung auch aus einer Hand kommen soll</h1>
    <p class="hero-text">Wir bieten Lösungen sowohl für Privatkunden, Geschäftskunden als auch Kommunen an, die schnell, fair und ohne Eigenleistung zu einer smarten Ladelösung für E-Fahrzeuge kommen möchten. Von der Beratung, über die Installation, Inbetriebnahme bis zur Abrechnung und Wartung bekommen Sie bei tanu-werk alles aus einer Hand.</p>
    <a class="btn-primary" href="#">Get Started</a>
  </div>
</section>

<section class="solutions">
  <div class="solution col-private">
    <h2>Als Privatkunde</h2>
    <div class="solution-box"><ul>
      <li>Bestandsanalyse mit umfangreicher Beratung über die Möglichkeiten der Umsetzung</li>
      <li>Prüfung und Übernahme der Anmeldung verfügbarer Fördermöglichkeiten</li>
      <li>Auswahl an smarten Wallbox Lösungen, passend für Ihr Fahrzeug und Ihre Bedürfnisse</li>
      <li>Installation inkl. aller notwendigen Materialien und Tätigkeiten (Durchbrüche, Erdarbeiten, etc.)</li>
      <li>Inbetriebnahme und Einweisung in die Ladetechnik</li>
      <li>Jährlich technische Wartung nach DGUV3</li>
      <li>Reparaturservice, unter Berücksichtigung der geltenden Garantie Ansprüche</li>
    </ul></div>
  </div>
  <div class="solution col-business">
    <h2>als Geschäftskunde</h2>
    <div class="solution-box is-featured"><ul>
      <li>Durchführung einer individuellen Bedarfsanalyse inkl. Ermittlung der Anforderungen für:</li>
      <li>Haus- und Immobilienverwaltungen Dienstleistungs- und Handelsunternehmen</li>
      <li>Hotel und Beherbergungsbetriebe Parkraum- und Parkhausbetreiber Tourismus, Sport- und Freizeiteinrichtungen</li>
      <li>Planung und Projektierung des Installationsaufwands inkl. Materialverbrauch</li>
      <li>Leasing oder Kauf der Hardware</li>
      <li>Normgerechte Installation der Ladeinfrastruktur inkl. Durchbruch-, Brandschutz- und Erdarbeiten</li>
      <li>Bei Bestandsbauten Integration der Ladeinfrastruktur in die Gebäudesystemtechnik und ggf. Anpassung des Netzanschlusses Inbetriebnahme der Anlage inkl. Prüf- und Messprotokollen</li>
      <li>Wiederkehrende technische Prüfung der Anlage nach DGUV 3</li>
      <li>Austausch und Reparatur Service</li>
      <li>Unterstützung bei der mtl. Nutzungsabrechnung und Einbindung in Ihre vorhandene Abrechnungssysteme</li>
      <li>ODER direkte Abrechnung mit den Nutzern</li>
    </ul></div>
  </div>
  <div class="solution col-community">
    <h2>als Kommune</h2>
    <div class="solution-box"><ul>
      <li>Konzeptionierung möglicher Ladeinfrastrukturen innerhalb Ihrer Gemeinde</li>
      <li>Planung und Projektsteuerung inkl. sämtlicher behördlicher Genehmigungsverfahren und Beantragung von Fördermitteln</li>
      <li>Fachgerechte Installation und Inbetriebnahme</li>
      <li>Regelmäßige Wartung gemäß Vorschrif</li>
      <li>Reparatur und Kundenservice</li>
      <li>Direkte Abrechnung mit dem Nutzer</li>
      <li>Beteiligung der Gemeinde am Umsatz</li>
      <li>Möglichkeit der Integration von Bonusprogrammen, mit denen der lokale Einzelhandel beworben wird</li>
    </ul></div>
  </div>
</section>

<footer class="site-footer">
  <div class="footer-brand"><span class="brand-dot"></span>tanu-werk.de</div>
  <nav class="footer-nav">
    <a href="#">Lösungen</a><a href="#">Unternehmen</a><a href="#">Services</a><a href="#">Karriere</a><a href="#">Kontakt</a>
  </nav>
  <div class="social" aria-label="Soziale Netzwerke">
    <span class="is-active"></span><span></span><span></span><span></span>
  </div>
  <p class="copyright">©Copyrights 2022 tanu-werk | &nbsp; All Rights Reserved</p>
</footer>
</body>
</html>
```